Small environmental consultancy requires basic yet awesome website design by aspiring and cool desig

We are a small environmental consultancy based in Australia, we have set-out a design brief for our website, using a logo we had completed here on Velto Marsh as well. We hope you can help us with a website!

Website must be wordpress friendly - we have reserved hosting with them already!

Number of Pages Required

4 page

Requirements
Must have
• use supplied logo
• wordpress
• follow provided brief

```html
<!DOCTYPE html>
<html lang="en">
<head>
<meta charset="utf-8">
<title>Terrane Advisors</title>
<link rel="stylesheet" href="https://fonts.googleapis.com/css2?family=Open+Sans:wght@400;600;700&family=Roboto+Condensed:wght@400;700&display=swap">
<style>
:root{
  --green:#8cbf3f;
  --green-dark:#6f9e2b;
  --ink:#2b2b2b;
  --dark:#333333;
  --darker:#262626;
  --grey:#ededed;
  --mid:#8a8a8a;
  --line:#dcdcdc;
  --white:#ffffff;
}
*{box-sizing:border-box;margin:0;padding:0}
html,body{width:1200px;height:2800px;overflow:hidden;background:var(--white)}
body{font-family:"Open Sans",Arial,sans-serif;color:var(--ink);font-size:13px;line-height:1.5}
.page{position:relative;width:1200px;height:2800px;overflow:hidden}
.heading{font-family:"Roboto Condensed","Arial Narrow",sans-serif;font-weight:700;font-size:34px;text-align:center;color:var(--ink);letter-spacing:.5px}
.subheading{text-align:center;color:var(--mid);font-size:13px;margin-top:2px}
.rule{width:60px;height:2px;background:var(--green);margin:10px auto 0}
.btn{display:inline-block;background:var(--green);color:var(--white);font-size:11px;font-weight:600;padding:5px 16px;text-transform:uppercase}

/* hero */
.hero{position:absolute;left:0;top:0;width:1200px;height:500px}
.hero-photo{position:absolute;inset:0;background:radial-gradient(ellipse at 30% 60%,#c9dfb0 0%,#9fc57a 35%,#6f9a4f 70%,#4f7438 100%)}
.topbar{position:absolute;left:0;top:0;width:1200px;height:70px;background:rgba(255,255,255,.95);display:flex;align-items:center;padding:0 150px}
.brand{display:flex;align-items:center;gap:10px}
.brand-mark{width:40px;height:40px;border-radius:50%;background:var(--green)}
.brand-name{font-family:"Open Sans",sans-serif;font-weight:700;font-size:18px;color:var(--green-dark)}
.top-email{margin-left:auto;font-size:12px;color:var(--mid);display:flex;align-items:center;gap:6px}
.social{display:flex;gap:6px;margin-left:24px}
.social span{width:22px;height:22px;background:#cfcfcf}
.nav{position:absolute;left:0;top:70px;width:1200px;height:42px;background:rgba(40,40,40,.85);padding-left:330px;display:flex}
.nav a{color:var(--white);font-size:12px;font-weight:600;text-decoration:none;padding:0 22px;line-height:42px;text-transform:uppercase}
.nav a.active{background:var(--green)}
.dropdown{position:absolute;left:525px;top:112px;width:220px;background:var(--green)}
.dropdown li{list-style:none;color:var(--white);font-size:11px;font-weight:600;padding:8px 14px;border-bottom:1px solid rgba(255,255,255,.35);text-transform:uppercase}
.hero-caption{position:absolute;left:760px;top:170px;width:300px;background:rgba(30,30,30,.75);color:var(--white);font-size:22px;line-height:1.35;padding:16px 20px}

/* intro */
.intro{position:absolute;top:500px;left:0;width:1200px;height:170px;background:var(--dark);display:flex;align-items:center;justify-content:center}
.intro p{width:900px;text-align:center;color:var(--white);font-size:22px;line-height:1.45}
.intro strong{color:var(--green);font-weight:600}

/* services */
.services{position:absolute;top:690px;left:0;width:1200px;height:440px}
.cards{display:flex;justify-content:center;gap:18px;margin-top:30px}
.card{width:240px;height:270px;border:1px solid var(--line);background:var(--white);text-align:center;padding:18px 16px;position:relative}
.card-icon{width:62px;height:62px;border:2px solid var(--green);border-radius:50%;margin:0 auto 10px;display:flex;align-items:center;justify-content:center}
.card h3{font-size:14px;font-weight:600;margin-bottom:8px;line-height:1.3}
.card p{font-size:11px;color:var(--mid);line-height:1.5}
.card .btn{position:absolute;bottom:16px;left:50%;transform:translateX(-50%)}
.card.featured{background:var(--green);color:var(--white);text-align:left;margin-top:-16px;height:290px;box-shadow:0 4px 10px rgba(0,0,0,.2)}
.card.featured .card-icon{background:var(--ink);border-color:var(--ink);border-radius:0;margin:0 0 10px}
.card.featured h3{color:var(--white)}
.card.featured li{list-style:none;font-size:12px;padding-left:14px;position:relative;margin-bottom:3px}
.card.featured li::before{content:"";position:absolute;left:0;top:7px;width:6px;height:6px;background:var(--white)}
.card.featured .btn{background:var(--white);color:var(--green-dark);left:16px;transform:none}
.services-more{text-align:center;margin-top:22px}

/* people */
.people{position:absolute;top:1140px;left:0;width:1200px;height:370px;background:var(--grey);padding-top:34px}
.people-row{display:flex;justify-content:center;gap:60px;margin-top:34px}
.person{width:420px;display:flex;gap:18px}
.portrait{width:140px;height:170px;flex:none;background:linear-gradient(160deg,#9cb3c6,#5d7185)}
.person h3{color:var(--green-dark);font-size:17px;font-weight:700}
.person .meta{font-size:11px;color:var(--mid);margin:4px 0 8px}
.person p{font-size:11px;color:#555}

/* partners */
.partners{position:absolute;top:1510px;left:0;width:1200px;height:160px;background:var(--darker);display:flex;align-items:center;justify-content:center;gap:40px;color:var(--white)}
.partner{width:380px;font-size:12px;line-height:1.5}
.partner.right{text-align:right}
.badge{display:inline-block;width:130px;height:40px;background:var(--white);margin-top:10px}
.partners-title{font-family:"Roboto Condensed",sans-serif;font-weight:700;font-size:16px;color:var(--green);letter-spacing:1px}

/* projects */
.projects{position:absolute;top:1690px;left:0;width:1200px;height:420px}
.gallery{display:flex;justify-content:center;gap:6px;margin-top:28px}
.gallery div{width:142px;height:250px}

/* clients */
.clients{position:absolute;top:2120px;left:0;width:1200px;height:250px}
.client-row{display:flex;justify-content:center;align-items:center;gap:34px;margin-top:40px}
.client-row span{width:110px;height:44px;background:#d6d6d6}
.client-row span.round{width:48px;border-radius:50%}

/* footer */
.footer{position:absolute;top:2400px;left:0;width:1200px;height:360px;background:var(--dark);color:#cfcfcf;display:flex;justify-content:center;gap:40px;padding-top:40px}
.footer-col{width:230px;font-size:11px;line-height:1.7}
.footer-col h4{color:var(--white);font-size:13px;font-weight:700;text-transform:uppercase;margin-bottom:10px;border-bottom:1px solid #555;padding-bottom:6px}
.field{height:24px;background:#4a4a4a;margin-bottom:6px}
.field.tall{height:54px}
.legal{position:absolute;top:2760px;left:0;width:1200px;height:40px;background:var(--darker);color:#aaa;font-size:11px;display:flex;align-items:center;justify-content:space-between;padding:0 150px}
.to-top{width:24px;height:24px;background:var(--green)}
</style>
</head>
<body>
<div class="page">

  <section class="hero">
    <div class="hero-photo" role="img" aria-label="Close-up photograph of a fresh green leaf with water droplets"></div>
    <header class="topbar">
      <div class="brand"><span class="brand-mark"></span><span class="brand-name">Terrane Advisors</span></div>
      <div class="top-email">
        <svg width="14" height="10" viewBox="0 0 14 10"><rect x=".5" y=".5" width="13" height="9" fill="none" stroke="#8a8a8a"/><path d="M.5 .5 7 6 13.5 .5" fill="none" stroke="#8a8a8a"/></svg>
        admin@terraneadvisors.example
      </div>
      <div class="social"><span></span><span></span><span></span><span></span></div>
    </header>
    <nav class="nav">
      <a href="#">Home</a><a href="#">About</a><a href="#" class="active">Services</a><a href="#">Clients</a><a href="#">Contact</a>
    </nav>
    <ul class="dropdown">
      <li>Project Management</li>
      <li>Contaminated Land</li>
      <li>Hazardous Materials &amp; Occupational Hygiene</li>
      <li>Environmental Assessment and Management</li>
    </ul>
    <div class="hero-caption">Terrane Advisors offer environmental services</div>
  </section>

  <section class="intro">
    <p><strong>Terrane Advisors</strong> is Client focussed, offering highly experienced consultants providing effective and innovative environmental solutions.</p>
  </section>

  <section class="services">
    <h2 class="heading">OUR SERVICES</h2>
    <p class="subheading">What we are doing</p>
    <div class="cards">
      <article class="card featured">
        <div class="card-icon"><svg width="26" height="30" viewBox="0 0 26 30"><rect x="2" y="4" width="22" height="25" fill="none" stroke="#fff" stroke-width="2"/><rect x="8" y="1" width="10" height="6" fill="#fff"/><path d="M7 15h12M7 20h12M7 25h8" stroke="#fff" stroke-width="2"/></svg></div>
        <h3>Project Management</h3>
        <ul>
          <li>Site assessment</li>
          <li>Scope and budget planning</li>
          <li>Contractor supervision</li>
          <li>Regulatory liaison</li>
          <li>Progress reporting</li>
          <li>Final closeout</li>
        </ul>
        <span class="btn">Read More</span>
      </article>
      <article class="card">
        <div class="card-icon"><svg width="30" height="30" viewBox="0 0 30 30"><path d="M3 24h24M6 24V14l9-7 9 7v10" fill="none" stroke="#8cbf3f" stroke-width="2"/></svg></div>
        <h3>Contaminated Land</h3>
        <p>We assess, manage and remediate soil and groundwater to return sites to safe, lasting use for owners.</p>
        <span class="btn">Read More</span>
      </article>
      <article class="card">
        <div class="card-icon"><svg width="30" height="30" viewBox="0 0 30 30"><circle cx="15" cy="15" r="4" fill="#8cbf3f"/><path d="M15 3v8M15 19v8M3 15h8M19 15h8" stroke="#8cbf3f" stroke-width="2"/></svg></div>
        <h3>Hazardous Materials &amp; Occupational Hygiene</h3>
        <p>Surveys, air monitoring and clear registers that protect workers and keep your sites compliant.</p>
        <span class="btn">Read More</span>
      </article>
      <article class="card">
        <div class="card-icon"><svg width="30" height="30" viewBox="0 0 30 30"><path d="M15 4c7 4 9 12 0 22C6 16 8 8 15 4z" fill="none" stroke="#8cbf3f" stroke-width="2"/><path d="M15 10v14" stroke="#8cbf3f" stroke-width="2"/></svg></div>
        <h3>Environmental Assessment and Management</h3>
        <p>Impact studies, approvals and practical management plans that guide your project from start to finish.</p>
        <span class="btn">Read More</span>
      </article>
    </div>
    <div class="services-more"><span class="btn">View All Services</span></div>
  </section>

  <section class="people">
    <h2 class="heading">OUR PEOPLE</h2>
    <div class="rule"></div>
    <div class="people-row">
      <article class="person">
        <div class="portrait" role="img" aria-label="Portrait photograph of consultant Liam Cartwright"></div>
        <div>
          <h3>Liam Cartwright</h3>
          <div class="meta">Principal Consultant<br>liam@terraneadvisors.example</div>
          <p>Liam has over twenty years of experience in contaminated land and hazardous materials across mining, industrial and government projects. He leads site investigations, remediation planning and occupational hygiene programs with a strong focus on clear advice and practical outcomes for clients.</p>
        </div>
      </article>
      <article class="person">
        <div class="portrait" role="img" aria-label="Portrait photograph of consultant Owen Hales"></div>
        <div>
          <h3>Owen Hales</h3>
          <div class="meta">Senior Consultant<br>owen@terraneadvisors.example</div>
          <p>Owen specialises in environmental assessment, approvals and management systems. He has guided infrastructure and development projects through regulatory processes and supports clients with monitoring, audits and reporting that meet every requirement.</p>
        </div>
      </article>
    </div>
  </section>

  <section class="partners">
    <div class="partner">
      We are proud to be associated with Southland Audit Group to support our clients with all audit services.
      <br><span class="badge"></span>
    </div>
    <div class="partners-title">OUR PARTNERS</div>
    <div class="partner right">
      We are proud to be associated with Coastal Safety Network to support delivery of hazardous materials services.
      <br><span class="badge"></span>
    </div>
  </section>

  <section class="projects">
    <h2 class="heading">OUR PROJECTS</h2>
    <div class="rule"></div>
    <div class="gallery">
      <div role="img" aria-label="Photograph of an industrial site at dusk" style="background:linear-gradient(#7b8794,#3c4550)"></div>
      <div role="img" aria-label="Photograph of workers in protective suits" style="background:linear-gradient(#e2e2dc,#9c9c94)"></div>
      <div role="img" aria-label="Photograph of soil sampling equipment" style="background:linear-gradient(#6f6450,#3d352a)"></div>
      <div role="img" aria-label="Photograph of yellow hazardous material drums" style="background:linear-gradient(#d8b23a,#8a6a1c)"></div>
      <div role="img" aria-label="Photograph of a remediated green field" style="background:linear-gradient(#9fc57a,#4f7438)"></div>
      <div role="img" aria-label="Photograph of a monitoring bore on a site" style="background:linear-gradient(#b6b9bc,#5e6266)"></div>
      <div role="img" aria-label="Photograph of an excavation works area" style="background:linear-gradient(#a58b6a,#5b4a35)"></div>
    </div>
  </section>

  <section class="clients">
    <h2 class="heading">OUR CLIENTS</h2>
    <div class="rule"></div>
    <div class="client-row">
      <span class="round"></span><span></span><span></span><span></span><span></span><span class="round"></span>
    </div>
  </section>

  <footer class="footer">
    <div class="footer-col">
      <h4>About Us</h4>
      Terrane Advisors is a small consultancy offering experienced, client focussed environmental advice and practical solutions for industry and government across the region.
    </div>
    <div class="footer-col">
      <h4>Contact Us</h4>
      12 Fern Street, Greenvale<br>PO Box 000, Greenvale<br>Phone: 0400 000 000<br>admin@terraneadvisors.example
    </div>
    <div class="footer-col">
      <h4>Quick Contact</h4>
      <div class="field"></div><div class="field"></div><div class="field tall"></div>
      <span class="btn">Send</span>
    </div>
    <div class="footer-col">
      <h4>Newsletter</h4>
      Sign up to receive our latest news and updates.
      <div class="field" style="margin-top:8px"></div>
      <span class="btn">Subscribe</span>
    </div>
  </footer>
  <div class="legal">
    <span>© Copyright Terrane Advisors</span>
    <span>Designed by Velto Marsh</span>
    <span class="to-top"></span>
  </div>

</div>
</body>
</html>
```